Dynamic Business Card for Sports Supplements Company

Hi! I'm looking for an awesome business card to match my existing sports supplement company. I have uploaded my current company logo and screenshot of the front page of my website.

I would like to have something dynamic and interesting and utilize the colors in the website - the reds and purples

The business card should be double sided and focus on a unique eye-catching design on the back and include all the relevant company info.

Most importantly, it should say somewhere: "Sign up on our website for a coupon code."

Target Market(s)

Mostly for women gym goers but it shouldn't be too feminine. It should be in keeping with the website design. It should flow and clearly be connected to it

Industry/Entity Type

Business

Contact Information for Business Card

Lorraine K. Vestal
CEO
LVestal@Quorvanexco.com
www.quorvanexco.com
555.417.3820
P.O. Box 47315
Tarrow Falls, Westmark 00000

Sign up on our website for a coupon code

Font styles to use
Serif
Sans Serif
Other font styles liked:
• Novecento font family and "Quorvanex" is in AR Destine font

Requirements
Must have
• One side should be a bold Quorvanex logo design. Even just the symbol itself may be o.k. (see attached file)

```html
<!DOCTYPE html>
<html lang="en">
<head>
<meta charset="utf-8">
<title>Quorvanex Business Card</title>
<link href="https://fonts.googleapis.com/css2?family=Source+Sans+3:ital,wght@0,400;0,600;0,700;1,400&display=swap" rel="stylesheet">
<style>
  :root {
    --backdrop: #e6e4e1;
    --card-black: #000000;
    --brand-red: #ec1c24;
    --white: #ffffff;
    --text-light: #f2f2f2;
    --divider: #3a3a3a;
  }
  * { margin: 0; padding: 0; box-sizing: border-box; }
  html, body {
    width: 1200px;
    height: 987px;
    overflow: hidden;
    background: var(--backdrop);
    font-family: "Source Sans 3", sans-serif;
  }
  .card {
    position: absolute;
    left: 293px;
    width: 615px;
    height: 351px;
    box-shadow: 0 3px 10px rgba(0,0,0,0.25);
    overflow: hidden;
  }
  /* Front */
  .card-front { top: 131px; background: var(--card-black); }
  .front-stripe-white {
    position: absolute; left: 0; right: 0; top: 320px; height: 4px;
    background: var(--white);
  }
  .front-stripe-red {
    position: absolute; left: 0; right: 0; top: 327px; bottom: 0;
    background: var(--brand-red);
  }
  .brand-lockup {
    position: absolute; left: 0; width: 298px; top: 178px;
    display: flex; align-items: center; justify-content: center; gap: 10px;
  }
  .brand-square {
    width: 18px; height: 18px; background: var(--brand-red);
  }
  .brand-name {
    color: var(--white);
    font-weight: 700;
    font-size: 31px;
    letter-spacing: 1px;
    line-height: 1;
  }
  .front-divider {
    position: absolute; left: 298px; top: 82px; width: 1px; height: 150px;
    background: var(--divider);
  }
  .contact-block {
    position: absolute; left: 321px; top: 82px;
    color: var(--text-light);
    font-size: 16px;
    line-height: 1;
  }
  .contact-name {
    color: var(--brand-red);
    font-size: 22px;
    font-weight: 600;
    letter-spacing: 0.5px;
    margin-bottom: 7px;
  }
  .contact-title { margin-left: 3px; margin-bottom: 16px; }
  .contact-address { margin-left: 3px; line-height: 23px; margin-bottom: 6px; }
  .contact-line {
    display: flex; align-items: center; gap: 8px;
    height: 23.5px; margin-left: 3px;
  }
  .contact-line svg { width: 14px; height: 14px; flex: none; }
  /* Back */
  .card-back {
    top: 506px; background: var(--brand-red);
    display: flex; flex-direction: column; align-items: center;
  }
  .back-brand {
    margin-top: 138px;
    color: var(--white);
    font-weight: 700;
    font-size: 62px;
    letter-spacing: 3px;
    line-height: 1;
  }
  .coupon-note {
    position: absolute; top: 290px; left: 0; right: 0;
    text-align: center;
    color: var(--white);
    font-style: italic;
    font-size: 16.5px;
  }
</style>
</head>
<body>
  <section class="card card-front">
    <div class="brand-lockup">
      <span class="brand-square"></span>
      <span class="brand-name">QUORVANEX</span>
    </div>
    <div class="front-divider"></div>
    <div class="contact-block">
      <p class="contact-name">LORRAINE K. VESTAL</p>
      <p class="contact-title">CEO</p>
      <p class="contact-address">P.O. Box 47315<br>Tarrow Falls, Westmark 00000</p>
      <p class="contact-line">
        <svg viewBox="0 0 16 16" aria-hidden="true"><path fill="#ec1c24" d="M3.6 1.2l2.3 2.6-1.4 1.7c.9 2 2.3 3.5 4.2 4.5l1.7-1.4 2.6 2.3-1.4 2.5C6.3 13.4 2.6 9.7 1.2 4z"/></svg>
        555.417.3820
      </p>
      <p class="contact-line">
        <svg viewBox="0 0 16 16" aria-hidden="true"><rect x="1" y="3" width="14" height="10" fill="#ec1c24"/><path d="M1.5 3.5L8 9l6.5-5.5" fill="none" stroke="#000" stroke-width="1.2"/></svg>
        LVestal@Quorvanexco.com
      </p>
      <p class="contact-line">
        <svg viewBox="0 0 16 16" aria-hidden="true"><circle cx="8" cy="8" r="7" fill="#ec1c24"/><path d="M4 5c2 0 2 2 3.5 2S8 9 6.5 10 6 13 6 13M10 3c0 2 2 2 2 4s2 1 2 1" fill="none" stroke="#000" stroke-width="1.2"/></svg>
        www.quorvanexco.com
      </p>
    </div>
    <div class="front-stripe-white"></div>
    <div class="front-stripe-red"></div>
  </section>

  <section class="card card-back">
    <p class="back-brand">QUORVANEX</p>
    <p class="coupon-note">Sign up on our website for a coupon code</p>
  </section>
</body>
</html>
```